Need a new company business card

I am looking for a new company business card. Front and back. With information on it as per below. Card should be professional. Yet clever. Simple. Modern design. Pim card, traditional size. OK with say, all black or all red backside.

Varnholt is an indie, bootstrapped magazine advancing the work of intersectional feminists busting their buts to create a just world through the power of enterprise and innovation.

Varnholt is the home and voice of entrepreneurial feminism and feminist innovators worldwide. Entrepreneurial feminists are people (of all genders) who see inequality as an innovation priority. They work to advance gender equity and/or who strive to integrate and practice feminist principles, pedagogy, values into their innovation and entrepreneurship work.
We are committed to this space being trans and queer inclusive, anti-racist, intersectional, brave, and safe. We welcome all allies. We value learning, edgy but civil discourse and integrative thinking skills.

Target Market(s)

feminists, business owners,

Industry/Entity Type

Publishing Company

Contact Information for Business Card

RD Tolliver
Founder/Publisher
4-237 Ashgrove Lane, Toronto, ON
M4T 2K8
publisher@varnholt.com
416-552-3019
www.varnholt.com

Font styles to use
Serif
Other font styles liked:
• Myriad Pro

Colors
ec1f27
000000
ffffff

Requirements
Must have
• logo
• use red, black white colours only.
Nice to have
• use the compass in pattern or creatively but not too busy please
Should not have
• Should not be too busy. Elegant.

```html
<!DOCTYPE html>
<html lang="en">
<head>
<meta charset="utf-8">
<title>Varnholt business card</title>
<link rel="stylesheet" href="https://fonts.googleapis.com/css2?family=Roboto:wght@400;500;700&display=swap">
<style>
  :root {
    --red: #d22420;
    --black: #161616;
    --ink: #2b2c2e;
    --white: #ffffff;
    --paper: #f4f4f4;
    --band-grey: #3a3b3d;
    --backdrop: #d6d6d6;
  }
  * { box-sizing: border-box; margin: 0; padding: 0; }
  html, body { width: 1200px; height: 1138px; overflow: hidden; }
  body { background: var(--backdrop); font-family: "Roboto", sans-serif; position: relative; }

  .card {
    position: absolute;
    width: 620px;
    height: 374px;
    border-radius: 16px;
    overflow: hidden;
  }
  .card--front { left: 274px; top: 186px; background: var(--black); }
  .card--back { left: 276px; top: 608px; background: var(--paper); }

  .wordmark {
    position: absolute;
    font-family: "Roboto", sans-serif;
    font-weight: 700;
    font-size: 88px;
    letter-spacing: -2px;
    line-height: 1;
  }
  .card--front .wordmark { left: 68px; top: 132px; color: var(--white); }
  .card--back .wordmark { left: 36px; top: 50px; color: var(--ink); }

  .tagline {
    position: absolute;
    font-family: "Roboto", sans-serif;
    font-weight: 500;
    font-size: 11.5px;
    letter-spacing: 1.2px;
    text-transform: uppercase;
    white-space: nowrap;
  }
  .card--front .tagline { left: 72px; top: 220px; color: var(--white); }
  .card--back .tagline { left: 40px; top: 140px; color: var(--ink); }

  .accent-band {
    position: absolute;
    right: 0; top: 0;
    width: 38px; height: 100%;
    background: var(--red);
  }

  .person { position: absolute; left: 38px; top: 274px; }
  .person__name { font-weight: 700; font-size: 23px; color: var(--ink); }
  .person__role { font-size: 15px; color: var(--red); margin-top: 4px; }

  .contact { position: absolute; left: 353px; color: var(--ink); font-size: 14.5px; line-height: 20px; font-style: normal; }
  .contact--address { top: 214px; }
  .contact--lines { top: 273px; }
  .contact__line { display: flex; align-items: center; gap: 10px; margin-left: 6px; }
  .contact__line svg { width: 14px; height: 14px; fill: var(--red); flex: none; }

  .footer-grey {
    position: absolute; left: 0; bottom: 0;
    width: 300px; height: 14px;
    background: var(--band-grey);
  }
  .footer-red {
    position: absolute; right: 0; bottom: 0;
    width: 344px; height: 46px;
    background: var(--red);
    clip-path: polygon(36px 0, 100% 0, 100% 100%, 0 100%);
  }
  .footer-red__url {
    position: absolute; left: 77px; top: 13px;
    color: var(--white); font-size: 15px;
  }
</style>
</head>
<body>
  <section class="card card--front" aria-label="Card front">
    <div class="wordmark">Varnholt</div>
    <p class="tagline">An indie magazine of entrepreneurial feminism</p>
    <div class="accent-band" aria-hidden="true"></div>
  </section>

  <section class="card card--back" aria-label="Card back">
    <div class="wordmark">Varnholt</div>
    <p class="tagline">An indie magazine of entrepreneurial feminism</p>

    <div class="person">
      <p class="person__name">RD Tolliver</p>
      <p class="person__role">Founder/Publisher</p>
    </div>

    <address class="contact contact--address">
      4-237 Ashgrove Lane,<br>Toronto, ON M4T 2K8
    </address>

    <div class="contact contact--lines">
      <p class="contact__line">
        <svg viewBox="0 0 16 16" aria-hidden="true"><path d="M2 5c0-2 2-3 6-3s6 1 6 3v1.5h-3V5H5v1.5H2zM4 8l2-1.5h4L12 8v5H4z"/></svg>
        416-552-3019
      </p>
      <p class="contact__line">
        <svg viewBox="0 0 16 16" aria-hidden="true"><path d="M1 3h14v10H1zM2.5 4.5 8 9l5.5-4.5v-0.2H2.5z" fill-rule="evenodd"/></svg>
        publisher@varnholt.com
      </p>
    </div>

    <div class="footer-grey" aria-hidden="true"></div>
    <div class="footer-red">
      <span class="footer-red__url">www.varnholt.com</span>
    </div>
  </section>
</body>
</html>
```